Skin cancer clinic services trifold brochure

Need trifold brochure listing skin cancer services our clinic provides, staff information, location and brief about skin cancer with colours similar to our web site www.Tolvarin.clinic. I will provide more information regarding services and staff but want this colourful and standout as it will be given to other referring doctors or patients

Target Market(s)

Age 40 to 80 years

Industry/Entity Type

Medical

Font styles to use
Serif

Colors

Designer to choose colors to be used in the design.

Requirements
Must have
• Logo, services, contact info, beach or sun look and colours similar to web site or logo

```html
<!DOCTYPE html>
<html lang="en">
<head>
<meta charset="utf-8">
<title>Tolvarin Skin Cancer Clinic – Trifold Brochure</title>
<link href="https://fonts.googleapis.com/css2?family=Noto+Serif:ital,wght@0,400;0,700;1,400&family=PT+Serif:ital,wght@0,400;0,700;1,400&display=swap" rel="stylesheet">
<style>
  :root{
    --backdrop:#6e6f73;
    --paper:#ffffff;
    --orange:#e2620f;
    --deep:#c8360b;
    --rust:#b52a08;
    --amber:#f0a21f;
    --accent:#e36a12;
    --ink:#3b3b3b;
    --haze:#fbeadb;
  }
  *{box-sizing:border-box;margin:0;padding:0}
  html,body{width:1200px;height:1200px;overflow:hidden}
  body{background:var(--backdrop);position:relative;font-family:"PT Serif",serif;color:var(--ink)}
  .brochure{position:absolute;left:30px;top:171px;width:1140px;height:857px;background:var(--paper);overflow:hidden}
  .bands{position:absolute;inset:0}
  .badge{position:absolute;border-radius:50%;background:var(--amber);display:flex;align-items:center;justify-content:center}
  .badge-ring{width:100%;height:100%;border-radius:50%;border:5px solid var(--paper);background:var(--orange);display:flex;align-items:center;justify-content:center;text-align:center;
    font-family:"Noto Serif",serif;color:#fff;font-weight:700;line-height:1.22}
  .badge-services{left:83px;top:13px;width:170px;height:170px;padding:4px}
  .badge-services .badge-ring{font-size:20px}
  .badge-treatments{left:502px;top:35px;width:150px;height:150px;padding:4px}
  .badge-treatments .badge-ring{font-size:19px}
  .badge-staff{left:886px;top:31px;width:140px;height:140px;padding:4px}
  .badge-staff .badge-ring{font-size:19px}

  .list{position:absolute;display:flex;flex-direction:column;font-size:9.4px;line-height:13.4px;text-align:justify}
  .list-services{left:52px;top:195px;width:304px;gap:11px}
  .list-treatments{left:434px;top:220px;width:305px;gap:11px}
  .item{position:relative}
  .item .sun{position:absolute;left:-30px;top:-2px;width:20px;height:20px}
  .item b{font-weight:700;color:var(--accent);font-size:10.6px}
  .item i{color:var(--accent)}
  .web-note{margin-top:10px}
  .web-note span{color:var(--accent)}

  .staff-intro{position:absolute;left:801px;top:206px;width:304px;font-size:10.8px;line-height:15.3px;text-align:justify}
  .staff-list{position:absolute;left:820px;top:287px;width:300px;list-style:none;font-family:"Noto Serif",serif}
  .staff-list li{position:relative;margin-bottom:12px;font-size:12.3px;line-height:17px}
  .staff-list .name{color:var(--accent)}
  .staff-list .creds{font-style:italic;color:#222;font-size:11.4px}
  .staff-list svg{position:absolute;left:-22px;top:2px;width:14px;height:22px}
  .staff-list li.tight{margin-bottom:12px}
  .side-note{position:absolute;left:783px;top:563px;width:132px;font-size:10.4px;line-height:15.2px;color:var(--accent);text-align:justify}
  .side-note p+p{margin-top:16px}
  .skin-figure{position:absolute;left:922px;top:505px;width:200px;height:240px;border-radius:6px;
    background:linear-gradient(180deg,#f6d6c3 0%,#e98a6a 35%,#d4553c 55%,#f4c24a 80%,#e87a3c 100%)}
</style>
</head>
<body>
<main class="brochure">
  <svg class="bands" viewBox="0 0 1140 857" width="1140" height="857" aria-hidden="true">
    <!-- panel one -->
    <polygon points="0,0 380,0 380,50 0,95" fill="var(--orange)"/>
    <polygon points="0,0 380,0 380,20 150,55" fill="var(--deep)"/>
    <polygon points="0,92 170,70 0,125" fill="var(--amber)"/>
    <polygon points="0,799 380,727 380,857 0,857" fill="var(--orange)"/>
    <polygon points="0,820 380,760 380,857 0,857" fill="var(--deep)"/>
    <polygon points="200,790 380,727 380,745" fill="var(--amber)"/>
    <!-- panel two -->
    <polygon points="380,0 760,0 760,148 600,90 380,57" fill="var(--orange)"/>
    <polygon points="380,0 760,0 760,70 560,25" fill="var(--deep)"/>
    <polygon points="380,727 760,813 760,857 380,857" fill="var(--orange)"/>
    <polygon points="380,727 760,805 760,820 380,745" fill="var(--amber)"/>
    <polygon points="380,780 760,857 380,857" fill="var(--deep)"/>
    <!-- panel three -->
    <polygon points="760,0 1140,0 1140,67 930,112 760,124" fill="var(--orange)"/>
    <polygon points="760,0 1140,0 1140,20 900,70" fill="var(--rust)"/>
    <polygon points="760,124 1140,67 1140,78 760,148" fill="var(--amber)"/>
    <polygon points="760,818 1140,751 1140,857 760,857" fill="var(--amber)"/>
    <polygon points="760,835 1140,778 1140,857 760,857" fill="var(--orange)"/>
    <polygon points="760,857 900,820 1140,857" fill="var(--deep)"/>
    <!-- fold shading -->
    <rect x="360" y="0" width="20" height="857" fill="#000" opacity="0.05"/>
    <rect x="740" y="0" width="20" height="857" fill="#000" opacity="0.07"/>
    <g role="img" aria-label="Faint sun motif decoration">
      <circle cx="778" cy="58" r="28" fill="var(--deep)" opacity="0.35"/>
      <circle cx="372" cy="807" r="30" fill="var(--deep)" opacity="0.3"/>
    </g>
    <defs>
      <symbol id="sun-icon" viewBox="0 0 20 20">
        <g fill="none" stroke="var(--accent)" stroke-width="1" stroke-linecap="round">
          <circle cx="10" cy="10" r="4"/>
          <path d="M10 1.5v3M10 15.5v3M1.5 10h3M15.5 10h3M4 4l2 2M14 14l2 2M4 16l2-2M14 6l2-2"/>
        </g>
      </symbol>
      <symbol id="scope-icon" viewBox="0 0 14 22">
        <g fill="none" stroke="#333" stroke-width="1.6" stroke-linecap="round">
          <path d="M2 1v6a5 5 0 0 0 10 0V1"/>
          <path d="M7 12v5a3 3 0 0 0 3 3"/>
          <circle cx="11" cy="20" r="1.3"/>
        </g>
      </symbol>
    </defs>
  </svg>

  <div class="badge badge-services"><div class="badge-ring">Professional<br>Skin<br>Services</div></div>
  <div class="badge badge-treatments"><div class="badge-ring">Specialised<br>Treatments</div></div>
  <div class="badge badge-staff"><div class="badge-ring">Our<br>Staff</div></div>

  <section class="list list-services">
    <div class="item"><svg class="sun"><use href="#sun-icon"/></svg><b>Advanced Skin Cancer Detection</b> with detailed Full Body skin checks using dermoscopy and technology to minimise unnecessary excisions.</div>
    <div class="item"><svg class="sun"><use href="#sun-icon"/></svg><b>Individual Mole mapping and full body photography</b> utilising intelligent skin analytics with <i><b>DermaTrace</b></i> – an artificial intelligence-powered platform which provides tools for documenting and diagnosing skin cancers and evidence-based care. Powered by AI algorithms, it will identify changes to the skin over time and support early clinical decisions and diagnosis.</div>
    <div class="item"><svg class="sun"><use href="#sun-icon"/></svg><b>SkinMapper Skin Imaging System</b> which captures high-quality images using SpectraScan – clinically proven technology which provides a unique level of detail and information from up to 2mm beneath the skin's surface allowing deeper assessment and risk of melanoma.</div>
    <div class="item"><svg class="sun"><use href="#sun-icon"/></svg><b>Purpose Built Skin Cancer Facility</b> providing Surgical treatments in 2 dedicated fully equipped theatres and Treatment room staffed by skilled skin cancer medicine nurses.</div>
    <div class="item"><svg class="sun"><use href="#sun-icon"/></svg><b>Large referral basis</b> for our patients that may require extensive therapy for their skin cancers, including Radiotherapy for cosmetically sensitive areas that are not optimally treated with surgery, Advanced care under the Melanoma Unit Harbourside or MOHs Surgery and more.</div>
    <div class="item"><svg class="sun"><use href="#sun-icon"/></svg><b>Priority Spot Checks</b> – appointments are set aside every day for urgent suspicious lesions allowing for quick evaluation, whether for an existing or new patient. Although we welcome GP referrals, it is not required.</div>
    <div class="item"><svg class="sun"><use href="#sun-icon"/></svg><b>GP Team Approach</b> – Tolvarin believes it is important that an integrated team approach to a patient's skin cancer care is important, and communication of histological results and findings are shared with their GP upon permission.</div>
    <div class="item"><svg class="sun"><use href="#sun-icon"/></svg><b>Pain minimisation Techniques</b> –Topical numbing creams and ChillPoint numbing agents are available to minimise tenderness that can come with local anaesthetics. Our theatres are equipped with overhead projectors playing calming nature scenes to ensure our patients are comfortable.</div>
  </section>

  <section class="list list-treatments">
    <div class="item"><svg class="sun"><use href="#sun-icon"/></svg><b>Surgical Procedures</b> – Our Doctors are proficient in surgical procedures from simple diagnostic biopsies or elliptical excisions to advanced procedures including skin grafts and surgical flap repair, all under a local anaesthetic.</div>
    <div class="item"><svg class="sun"><use href="#sun-icon"/></svg><b>Radiatome Radiofrequency procedures</b> – Surgical options include a high frequency radiosurgical device for scalpel-less surgery. It allows our Doctors to use Radiowaves instead of scalpels to provide advanced skin cancer surgical procedures or cosmetic procedures; including removal of spider veins or vascular lesions and benign non-suspicious moles, skin tags, seborrheic keratoses, warts and other raised lesions. A Radiatome procedure ensures minimal thermal tissue damage, bleeding, and recovery time, thus enhancing cosmetic outcome.</div>
    <div class="item"><svg class="sun"><use href="#sun-icon"/></svg><b>Margin Controlled Surgery</b><br>(also known as Slow Mohs or Delayed Closure) – a process where aggressive skin cancers are not closed after excision until the histological status and clearance is known. This can minimise the need for larger excisions and potentially benefit cosmetic outcome; especially in cosmetically sensitive regions such as the nose, ears and face.</div>
    <div class="item"><svg class="sun"><use href="#sun-icon"/></svg><b>Non-surgical treatments and preventative therapy options</b> – Our goal is to prevent and treat skin cancer in the least invasive way possible as appropriate. This includes preventative care including Vitamin B3 benefits and sun safe practices - to topical therapies, such as liquid nitrogen and prescriptive therapy for solar keratoses or superficial Non-Melanoma skin cancers.</div>
    <div class="item"><svg class="sun"><use href="#sun-icon"/></svg><b>Cosmetic Services</b> - Tolvarin approaches our skin cancer patient holistically and, by appointment, we can offer advice and treatment regarding skin pigmentation, troublesome bumps and lumps and more!</div>
    <p class="web-note">Please see our web site at <span>www.Tolvarin.clinic</span> for more information.</p>
  </section>

  <p class="staff-intro">At Tolvarin Skin Cancer Clinic, our highly qualified administrative staff, nurses and doctors are an integral art of the team ensuring excellent clinical care is provided to our patients. We currently have 5 experienced local octors:</p>

  <ul class="staff-list">
    <li><svg><use href="#scope-icon"/></svg><span class="name">Dr. Maren Holloway, BMed, FRACGP,</span><br><span class="creds">Diploma Skin Cancer Medicine/Surgery,<br>Diploma Aesthetic Medicine</span></li>
    <li><svg><use href="#scope-icon"/></svg><span class="name">Dr. Priya Castellan, BMed, FRACGP,</span><br><span class="creds">Diploma Skin Cancer Medicine/Surgery</span></li>
    <li class="tight"><svg><use href="#scope-icon"/></svg><span class="name">Dr. Lena Whitcombe, MBBS, FRACGP</span></li>
    <li><svg><use href="#scope-icon"/></svg><span class="name">Dr. Owen Tasker, MBBS (Syd), Dip Law</span></li>
    <li><svg><use href="#scope-icon"/></svg><span class="name">Dr. Rosa Fennimore, MBBS (Hons), FRACGP,</span><br><span class="creds">Cert. Skin Cancer Medicine</span></li>
  </ul>

  <div class="side-note">
    <p>Early detection of skin cancers is vital for the best outcome.</p>
    <p>Tolvarin has invested in technology and research to provide the latest diagnostic services and treatments to meet the needs of our patients.</p>
  </div>

  <div class="skin-figure" role="img" aria-label="Illustration of a skin cross-section showing a lesion, hair follicles, blood vessels and fat layers"></div>
</main>
</body>
</html>
```